Halvick Ledgers & Advisory Tri-Fold Brochure (8.5"x11")

I need a professional looking brochure for my bookkeeping business. I am looking for something professional yet casual (not too corporate looking). I have attached a sample brochure that will outline the areas and a copy of our logo. I'd like to stick with shades of blue. The final product should communicate professional and personal.

Target Market(s)

Small service businesses.

Industry/Entity Type

Business

Font styles to use
Sans Serif

Requirements
Must have
• Professional looking photos of people in areas where it asks for a picture.

```html
<!DOCTYPE html>
<html lang="en">
<head>
<meta charset="utf-8">
<title>Halvick Ledgers &amp; Advisory – Brochure Cover</title>
<link rel="stylesheet" href="https://fonts.googleapis.com/css2?family=Open+Sans:wght@400;600;700&display=swap">
<style>
  :root {
    --page-bg: #d6d8da;
    --paper: #f4f5f6;
    --paper-shade: #e3e5e8;
    --sun: #f5c21b;
    --sun-deep: #f0a81c;
    --slate: #8a8c8f;
    --sky: #3aa5de;
    --sky-light: #8fd0f1;
    --sky-deep: #1f78c1;
    --ink-grey: #6b6d70;
    --footer: #4a4b4d;
    --white: #ffffff;
    --brand-blue: #1d6fae;
  }
  * { box-sizing: border-box; margin: 0; padding: 0; }
  html, body { width: 1097px; height: 1200px; overflow: hidden; }
  body {
    background: var(--page-bg);
    font-family: "Open Sans", Arial, sans-serif;
    position: relative;
  }
  .brochure-cover {
    position: absolute;
    left: 118px; top: 43px;
    width: 860px; height: 1113px;
    background: linear-gradient(160deg, var(--white) 0%, var(--paper) 45%, var(--paper-shade) 100%);
    overflow: hidden;
    box-shadow: 0 4px 18px rgba(0,0,0,.18);
  }
  .decor-field {
    position: absolute; left: 0; right: 0; top: 300px; bottom: 78px;
    background:
      radial-gradient(ellipse 70% 60% at 15% 75%, rgba(31,120,193,.85), rgba(31,120,193,0) 70%),
      radial-gradient(ellipse 50% 60% at 95% 60%, rgba(58,165,222,.75), rgba(58,165,222,0) 70%),
      linear-gradient(180deg, rgba(143,208,241,0) 0%, rgba(143,208,241,.55) 45%, rgba(58,165,222,.75) 100%);
  }
  .service-band {
    position: absolute; left: 184px; top: 40px; right: 0; height: 100px;
    display: flex;
  }
  .service-band .band-sun { width: 376px; background: linear-gradient(90deg, var(--sun-deep), var(--sun)); }
  .service-band .band-slate { width: 57px; background: var(--slate); }
  .service-band .band-sky { flex: 1; background: var(--sky); }
  .service-line {
    position: absolute; left: 200px; top: 100px;
    color: var(--white); font-size: 21px; letter-spacing: .5px;
    text-transform: uppercase; white-space: nowrap;
  }
  .values-line {
    position: absolute; right: 84px; top: 210px;
    color: var(--ink-grey); font-size: 31px; font-weight: 600; letter-spacing: .3px;
  }
  .photo-frame {
    position: absolute; background: var(--white); padding: 12px;
    box-shadow: 0 6px 14px rgba(0,0,0,.22);
  }
  .photo-frame .photo-fill { width: 100%; height: 100%; }
  .photo-meeting { left: 55px; top: 335px; width: 350px; height: 262px; transform: rotate(-9deg); }
  .photo-meeting .photo-fill { background: linear-gradient(135deg, #e8ecef, #a9b2bb 60%, #6f7a86); }
  .photo-team { left: 88px; top: 612px; width: 432px; height: 250px; transform: rotate(-3deg); }
  .photo-team .photo-fill { background: linear-gradient(180deg, #dfe7ee 0%, #b9c7d3 45%, #3b4450 100%); }
  .brand-badge {
    position: absolute; left: 435px; top: 308px; width: 400px; height: 400px;
    border-radius: 50%;
    background: rgba(255,255,255,.55);
    border: 22px solid var(--sky);
    box-shadow: 0 0 0 6px rgba(143,208,241,.6);
    display: flex; align-items: center; justify-content: center;
  }
  .brand-badge .badge-core {
    width: 300px; height: 300px; border-radius: 50%;
    background: var(--white);
    display: flex; flex-direction: column; align-items: center; justify-content: center;
    text-align: center; gap: 14px;
  }
  .brand-name {
    color: var(--brand-blue); font-size: 26px; font-weight: 700; line-height: 1.2;
    text-transform: uppercase; padding: 0 26px;
  }
  .brand-place { color: var(--brand-blue); font-size: 26px; font-weight: 700; }
  .contact-bar {
    position: absolute; left: 0; right: 0; bottom: 0; height: 78px;
    background: var(--footer);
    display: flex; align-items: center; gap: 46px; padding-left: 56px;
    color: var(--white); font-size: 18px;
  }
  .contact-item { display: flex; align-items: center; gap: 12px; white-space: nowrap; }
  .contact-item svg { width: 28px; height: 28px; }
</style>
</head>
<body>
  <main class="brochure-cover">
    <div class="decor-field" role="img" aria-label="Decorative abstract blue wave pattern"></div>

    <div class="service-band" aria-hidden="true">
      <div class="band-sun"></div><div class="band-slate"></div><div class="band-sky"></div>
    </div>
    <p class="service-line">Expert Bookkeeping Services for Small Businesses</p>
    <p class="values-line">Trustworthy Experienced&nbsp; Reliable</p>

    <figure class="photo-frame photo-meeting">
      <div class="photo-fill" role="img" aria-label="Photo of a business meeting table with papers, charts and coffee cups"></div>
    </figure>
    <figure class="photo-frame photo-team">
      <div class="photo-fill" role="img" aria-label="Photo of a smiling team of four professionals in business attire"></div>
    </figure>

    <div class="brand-badge">
      <div class="badge-core">
        <p class="brand-name">Halvick Ledgers &amp; Advisory</p>
        <p class="brand-place">Marrow Valley, PA</p>
      </div>
    </div>

    <footer class="contact-bar">
      <span class="contact-item">
        <svg viewBox="0 0 30 30" aria-hidden="true"><circle cx="15" cy="15" r="13" fill="none" stroke="#fff" stroke-width="2"/><path d="M10 8 l3 0 l1.5 4 l-2 1.5 c1 2 2 3 4 4 l1.5-2 l4 1.5 l0 3 c-7 1-13-5-12-12z" fill="#fff"/></svg>
        555.214.0387
      </span>
      <span class="contact-item">
        <svg viewBox="0 0 30 30" aria-hidden="true"><circle cx="15" cy="15" r="13" fill="none" stroke="#fff" stroke-width="2"/><text x="15" y="20.5" text-anchor="middle" font-size="15" font-weight="700" fill="#fff" font-family="Open Sans, sans-serif">@</text></svg>
        mara@halvickledgers.com
      </span>
      <span class="contact-item">
        <svg viewBox="0 0 30 30" aria-hidden="true"><circle cx="15" cy="15" r="13" fill="none" stroke="#fff" stroke-width="2"/><circle cx="15" cy="15" r="8" fill="none" stroke="#fff" stroke-width="1.6"/><ellipse cx="15" cy="15" rx="3.5" ry="8" fill="none" stroke="#fff" stroke-width="1.4"/><path d="M7 15 h16" stroke="#fff" stroke-width="1.4"/></svg>
        www.yourwebsite.com
      </span>
    </footer>
  </main>
</body>
</html>
```